Web Design Project

Psychotherapy and Counselling Practice needs a landing page web design.

My business "Larkfield Advisory" specialises in the treatment of Anxiety and Depression with a holistic approach, endeavouring to unlock the key that holds us to ransom in a life that is imbalanced, frustrating, and ultimately of our own making due to our own perceptions and behaviours.

There is much that impacts us which we cannot change, but we are always in control of how we think, and how we frame our experiences.....learning to challenge those thoughts and behaviours that are destructive and disempowering opens up a world of joyful possibility. Life is about making choices, learn to make wiser and healthier choices.......

Larkfield Advisory has a client base of individual clients but will seek to expand to offer services to the Corporate world by offering an adjunct to employers for established "Wellness Programs".

Larkfield Advisory is a highly professional, ethically bound business, with the needs of the client at the forefront of all we do.

Larkfield Advisory wishes to avoid the usual "jargon driven" psychobabble offered on many counselling web pages. It aims to be stylishly presented, clean in look and with as few "words" as possible and a largely white background (faster loading and more powerful impact of what is stated), those words contained in the webpage should be meaningful, persuasive and have an impact simply at glance. Larkfield does not want , or expect, those prospective clients in need of support , to be reading through volumes of industry driven cliches.

At this point Larkfield is just looking for a high quality landing page. However in time this will likely expand to include other sections such as case studies, video content etc.

Target Market(s)

Those in need of emotional support, suffering mental health issues, and those simply wanting to become self aware supported by a mindful therapist.

Industry/Entity Type

Industry

Requirements
Must have
• The design must incorporate the Larkfield logo and colour schemes found on the attached files.

```html
<!DOCTYPE html>
<html lang="en">
<head>
<meta charset="utf-8">
<title>Larkfield Advisory</title>
<link rel="stylesheet" href="https://fonts.googleapis.com/css2?family=Arimo:ital,wght@0,400;0,700;1,400&display=swap">
<style>
:root{
  --green:#8aad18;
  --green-dark:#6f8f0c;
  --heading:#7f9c10;
  --text:#6a6a6a;
  --dark:#222;
  --panel:#efefef;
  --white:#fff;
}
*{box-sizing:border-box;margin:0;padding:0}
html,body{width:1062px;height:1200px;overflow:hidden}
body{font-family:"Arimo",Arial,sans-serif;background:linear-gradient(#a3a3a3,#6b6b6b);position:relative;color:var(--text);font-size:12.5px}
.abs{position:absolute}
.header{left:0;top:0;width:1062px;height:166px;background:var(--white);border-bottom:5px solid var(--green)}
.brand{left:80px;top:80px;font-size:27px;color:var(--green);letter-spacing:1px}
.brand-dot{left:80px;top:64px;width:10px;height:10px;background:var(--green);border-radius:50%}
.portrait{left:665px;top:17px;width:83px;height:86px;border:4px solid #ddd;border-radius:3px;background:linear-gradient(#d8d8d8,#8a8a8a)}
.name{left:763px;top:13px;font-size:21px;color:#777}
.creds{left:763px;top:40px;font-size:13px;color:#777}
.contact{left:763px;font-size:13px;color:var(--green-dark)}
.contact b{font-weight:400;font-size:15px}
.nav{left:474px;top:126px;width:509px;height:40px;background:linear-gradient(#9dbf27,#7e9f12);border-radius:4px 4px 0 0;display:flex}
.nav a{flex:auto;color:#fff;text-decoration:none;font-size:13px;text-align:center;line-height:42px;border-right:1px solid #6f8d0c;border-left:1px solid #a8c83a}
.nav a:first-child{border-left:0}.nav a:last-child{border-right:0}
.sheet{left:79px;top:175px;width:904px;height:940px;background:var(--white)}
.slider{left:85px;top:177px;width:892px;height:299px;background:#0c0c0c;border-radius:3px;overflow:hidden}
.slide-photo{left:0;top:0;width:520px;height:299px;background:linear-gradient(90deg,#6a6a66,#4a4a47 55%,#0c0c0c)}
.slide-title{left:543px;top:40px;color:#93b81c;font-size:24px;font-weight:700}
.slide-sub{left:543px;top:68px;color:#fff;font-size:22px;font-weight:700}
.slide-text{left:543px;top:104px;width:300px;color:#ccc;font-size:12.5px;line-height:20px;text-align:justify}
.btn{left:543px;top:180px;width:139px;height:34px;background:linear-gradient(#9a9a9a,#5d5d5d);border-radius:3px;color:#fff;font-weight:700;font-size:14px;line-height:34px;padding-left:12px}
.btn i{position:absolute;right:12px;top:9px;width:16px;height:16px;border-radius:50%;background:#444;color:#fff;font-style:normal;font-size:11px;line-height:16px;text-align:center}
.dot{top:258px;width:18px;height:18px;border-radius:50%;border:2px solid #ddd;background:#777}
.dot.on{background:var(--green)}
.shadow{left:90px;top:480px;width:880px;height:24px;background:radial-gradient(ellipse at top,rgba(0,0,0,.18),transparent 70%)}
h2{position:absolute;color:var(--heading);font-size:18.5px;font-weight:700}
.para{position:absolute;line-height:20.3px;text-align:justify;font-size:12.5px}
.rule{left:90px;top:689px;width:608px;height:1px;background:#e2e2e2}
.card{top:808px;width:184px;height:212px;background:var(--panel);border-radius:3px}
.card .pic{position:absolute;left:6px;top:6px;width:172px;height:108px;border-radius:3px}
.card p{position:absolute;left:15px;top:124px;width:160px;line-height:18.5px;font-size:12.5px}
.card .more{position:absolute;left:15px;top:193px;font-size:10.5px;font-weight:700;color:var(--dark)}
.news{left:718px;width:253px;height:108px;background:var(--panel);border-radius:3px;padding:11px 15px}
.news p{line-height:20.3px;text-align:justify;font-size:12.5px}
.news span{display:block;color:var(--dark);margin-top:3px}
.arrow{width:16px;height:16px;border-radius:50%;background:#c4c4c4;color:#fff;font-size:11px;line-height:16px;text-align:center}
.testi{left:718px;top:941px;width:253px;height:158px;background:var(--panel);border-radius:3px;padding:16px 15px}
.testi p{font-style:italic;line-height:20.3px;text-align:justify;font-size:12.5px}
.testi q{quotes:none}
.testi .mark{font-style:normal;font-weight:700;color:#555;font-size:20px;line-height:10px}
.testi span{display:block;color:var(--dark);margin-top:6px}
.newsletter{left:94px;top:1036px;width:602px;height:64px;background:linear-gradient(#6f6f6f,#4e4e4e);border-radius:3px}
.envelope{left:26px;top:18px;width:38px;height:26px}
.nl-title{left:76px;top:20px;color:#fff;font-size:20px;font-weight:700}
.field{left:282px;top:14px;width:296px;height:36px;background:#fff;border-radius:2px;color:#888;font-size:13px;line-height:36px;padding-left:14px}
.submit{left:486px;top:3px;width:96px;height:30px;background:linear-gradient(#555,#222);border-radius:2px;color:#fff;font-weight:700;font-size:14.5px;text-align:center;line-height:30px}
.footer-links{left:79px;top:1134px;color:#fff;font-size:13px;word-spacing:3px}
.copy{left:79px;top:1164px;color:#fff;font-size:13px;word-spacing:2px}
.social{top:1148px;width:22px;height:22px;border-radius:3px;background:#dcdcdc}
</style>
</head>
<body>
<header class="abs header">
  <span class="abs brand-dot"></span>
  <div class="abs brand">Larkfield</div>
  <div class="abs portrait" role="img" aria-label="Portrait photo of the practitioner"></div>
  <div class="abs name">Rowan Ellery BA</div>
  <div class="abs creds">(Psych) BSc (Hons) Psych MBPS</div>
  <div class="abs contact" style="top:66px">Mobile : 0400 123 987</div>
  <div class="abs contact" style="top:89px">E-mail : <b>rowan.ellery@larkfieldmail.com</b></div>
  <nav class="abs nav"><a>Home</a><a>About us</a><a>Services</a><a>Programs</a><a>Seminars</a><a>Contact us</a></nav>
</header>

<div class="abs sheet"></div>

<section class="abs slider">
  <div class="abs slide-photo" role="img" aria-label="Photo of a person sitting alone, head resting on knees"></div>
  <div class="abs slide-title">ANXIETY AND DEPRESSION</div>
  <div class="abs slide-sub">Approach consulting</div>
  <p class="abs slide-text">Donec vestibulum turpis lorem, vitae vulputate justo pharetra ut. Cras justo erat, venenatis eget odio ut, posuere semper magna.</p>
  <div class="abs btn">CONTACT US<i>›</i></div>
  <span class="abs dot on" style="left:775px"></span>
  <span class="abs dot" style="left:803px"></span>
  <span class="abs dot" style="left:832px"></span>
  <span class="abs dot" style="left:860px"></span>
</section>
<div class="abs shadow"></div>

<h2 style="left:93px;top:517px">Welcome to Larkfield</h2>
<p class="para" style="left:93px;top:547px;width:604px">Cras vestibulum a massa at pharetra. Nunc sed lacinia velit, eu commodo elit. Maecenas porta nec velit in pharetra. Cras tortor neque, pretium ut nibh a, facilisis iaculis arcu. Interdum et malesuada fames ac ante ipsum primis in faucibus. Curabitur gravida metus ut urna dapibus vulputate eget sed sem. Aenean tincidunt, tortor at tris tique condimentum, felis neque mollis massa, quis interdum eros leo ac est. Donec sit amet odio eget nibh convallis ultricies. Cum sociis natoque penatibus et magnis dis parturient montes,c</p>
<div class="abs rule"></div>

<h2 style="left:92px;top:705px">Our Research</h2>
<p class="para" style="left:93px;top:736px;width:604px">Nam fringilla sollicitudin dui. Cras hendrerit convallis fringilla. Cras in dignissim metus, vel auctor velit. Vestibulum sed rutrum leo. Ut ac massa ligula. Aliquam semper, mi id eleifend consectetur, libero velit congue nibh, et porttitor sapien arcu a mauris. Donec volutpat vel lectus id varius.</p>

<article class="abs card" style="left:94px">
  <div class="pic" role="img" aria-label="Photo of a person meditating by the sea at sunset" style="background:linear-gradient(#8fa9c4,#d9c7a0 60%,#3a3a3a)"></div>
  <p>Aliquam mi eleifend consect etur, libero velit congue nibh, et porttitor sapien.</p>
  <span class="more">VIEW MORE&nbsp; »</span>
</article>
<article class="abs card" style="left:304px">
  <div class="pic" role="img" aria-label="Black and white photo of a person sitting on stairs" style="background:linear-gradient(120deg,#2a2a2a,#8a8a8a 60%,#cfcfcf)"></div>
  <p>Aliquam mi eleifend consect etur, libero velit congue nibh, et porttitor sapien.</p>
  <span class="more">VIEW MORE&nbsp; »</span>
</article>
<article class="abs card" style="left:513px">
  <div class="pic" role="img" aria-label="Photo of two people doing a yoga pose" style="background:linear-gradient(#fafafa,#e9e6e2)"></div>
  <p>Aliquam mi eleifend consect etur, libero velit congue nibh, et porttitor sapien.</p>
  <span class="more">VIEW MORE&nbsp; »</span>
</article>

<section class="abs newsletter">
  <svg class="abs envelope" viewBox="0 0 38 26"><rect x="1" y="1" width="36" height="24" fill="#f2f2f2" stroke="#bbb"/><path d="M1 1 19 15 37 1" fill="none" stroke="#aaa" stroke-width="1.5"/></svg>
  <div class="abs nl-title">Newsletter Subscribe</div>
  <div class="abs field">Enter your mail ID</div>
  <div class="abs submit" style="left:486px;top:17px">Subscribe</div>
</section>

<h2 style="left:719px;top:517px">Latest News &amp; Events</h2>
<span class="abs arrow" style="left:940px;top:517px">›</span>
<div class="abs news" style="top:552px"><p>Tnascetur ridiculus mus. Aenean pharetra neque vel est hendrerit dapibus. Morbi dapibus metus ac nisi ultricies.</p><span>Jun-12-2013</span></div>
<div class="abs news" style="top:667px"><p>Tnascetur ridiculus mus. Aenean pharetra neque vel est hendrerit dapibus. Morbi dapibus metus ac nisi ultricies.</p><span>Jun-12-2013</span></div>
<div class="abs news" style="top:780px"><p>Tnascetur ridiculus mus. Aenean pharetra neque vel est hendrerit dapibus. Morbi dapibus metus ac nisi ultricies.</p><span>Jun-12-2013</span></div>

<h2 style="left:719px;top:905px">Client’s Testimonials</h2>
<span class="abs arrow" style="left:940px;top:905px">›</span>
<div class="abs testi"><p><span class="mark" style="display:inline">“</span> Phasellus et magna id ante egestas henlibero, a sagittis lorem porta vitae. Quisque dapibus turpis fringilla, eget commodo felis interdum. Sed blandit felis ipsum, sed quam orci, et cursus <span class="mark" style="display:inline">”</span></p><span>Client name, City</span></div>

<div class="abs footer-links">Home &nbsp;| &nbsp;About us &nbsp;| &nbsp;Services &nbsp;| &nbsp;Programs &nbsp;| &nbsp;Seminars &nbsp;| &nbsp;Contact us</div>
<div class="abs copy">Copyright &copy; 2013 &nbsp; www.larkfieldadvisory.com.au &nbsp; All rights reserved.</div>
<span class="abs social" style="left:935px"></span>
<span class="abs social" style="left:962px"></span>
</body>
</html>
```